Business card design

Hi,
I need to have a business card design based on the current logo.
If competitive I not put it out to everyone.

It can be single of double sided

Target Market(s)

Food businesses

Industry/Entity Type

Food Manufacturing

Contact Information for Business Card

Details will on card will be as follows Name = Marcus Bell Email = Marcus@PanHearth.com.au Phone = 0418563207 Address = 57 Larkin Street , Fortitude Valley QLD 4006 Australia

Font styles to use
Other font styles liked:
• based on two fonts - Adelle & Museo

Requirements
Must have
• Based on the on switch concept

```html
<!DOCTYPE html>
<html lang="en">
<head>
<meta charset="utf-8">
<title>PanHearth Business Card</title>
<link rel="stylesheet" href="https://fonts.googleapis.com/css2?family=Nunito:wght@400;600;800&family=Zilla+Slab:wght@500&display=swap">
<style>
  :root {
    --canvas: #d9d9d9;
    --card-white: #ffffff;
    --card-dark: #2b1a1c;
    --brand-red: #e8163a;
    --ink: #2b1a1c;
    --text-light: #ffffff;
    --divider: #6a5557;
  }
  * { margin: 0; padding: 0; box-sizing: border-box; }
  html, body {
    width: 1200px;
    height: 800px;
    overflow: hidden;
    background: var(--canvas);
    font-family: "Nunito", sans-serif;
  }
  .stage {
    width: 1200px;
    height: 800px;
    display: flex;
    align-items: center;
    justify-content: center;
    gap: 40px;
  }
  .card {
    position: relative;
    width: 540px;
    height: 310px;
    border-radius: 16px;
    overflow: hidden;
    box-shadow: 0 6px 18px rgba(0,0,0,0.18);
  }
  .card-front { background: var(--card-white); }
  .front-bands { position: absolute; inset: 0; }

  .brand {
    position: absolute;
    left: 40px;
    top: 42px;
    display: flex;
    align-items: center;
    gap: 12px;
  }
  .brand-dot {
    width: 30px;
    height: 30px;
    border-radius: 50%;
    background: var(--brand-red);
  }
  .brand-name {
    font-weight: 800;
    font-size: 42px;
    letter-spacing: 1px;
    color: var(--ink);
    line-height: 1;
  }
  .tagline {
    position: absolute;
    left: 82px;
    top: 92px;
    font-family: "Zilla Slab", serif;
    font-weight: 500;
    font-size: 15px;
    color: var(--ink);
  }

  .person {
    position: absolute;
    left: 40px;
    top: 222px;
  }
  .person-name {
    font-weight: 800;
    font-size: 22px;
    letter-spacing: 1px;
    text-transform: uppercase;
    color: var(--brand-red);
  }
  .person-email {
    font-size: 14px;
    color: var(--text-light);
    margin-top: 2px;
  }
  .divider {
    position: absolute;
    left: 305px;
    top: 208px;
    width: 1px;
    height: 78px;
    background: var(--divider);
  }
  .address {
    position: absolute;
    left: 324px;
    top: 206px;
    font-style: normal;
    font-size: 13px;
    line-height: 1.45;
    color: var(--text-light);
  }
  .phone {
    display: flex;
    align-items: center;
    gap: 5px;
  }
  .phone-icon { width: 11px; height: 11px; }

  .card-back { background: var(--brand-red); }
  .back-brand {
    position: absolute;
    left: 0;
    right: 0;
    top: 112px;
    display: flex;
    align-items: center;
    justify-content: center;
    gap: 16px;
  }
  .back-dot {
    width: 56px;
    height: 56px;
    border-radius: 50%;
    background: var(--card-dark);
  }
  .back-name {
    font-weight: 800;
    font-size: 46px;
    letter-spacing: 1px;
    color: var(--text-light);
    line-height: 1;
  }
  .website {
    position: absolute;
    left: 0;
    right: 0;
    bottom: 40px;
    text-align: center;
    font-size: 15px;
    font-weight: 600;
    letter-spacing: 6px;
    text-transform: uppercase;
    color: var(--text-light);
  }
</style>
</head>
<body>
  <main class="stage">
    <section class="card card-front" aria-label="Card front">
      <svg class="front-bands" viewBox="0 0 540 310" width="540" height="310" aria-hidden="true">
        <path d="M0 194 L290 194 C370 194 395 112 470 112 L540 112 L540 310 L0 310 Z" fill="var(--card-dark)"/>
        <path d="M0 185 L290 185 C370 185 395 103 470 103 L540 103" fill="none" stroke="var(--brand-red)" stroke-width="4"/>
      </svg>

      <div class="brand">
        <span class="brand-dot"></span>
        <span class="brand-name">PANHEARTH</span>
      </div>
      <p class="tagline">Fresh Kitchen Supply Daily</p>

      <div class="person">
        <p class="person-name">Marcus Bell</p>
        <p class="person-email">Marcus@PanHearth.com.au</p>
      </div>

      <span class="divider"></span>

      <address class="address">
        57 Larkin Street<br>
        Harlow Heights<br>
        QLD 4178 Australia<br>
        <span class="phone">
          <svg class="phone-icon" viewBox="0 0 24 24" aria-hidden="true">
            <path fill="var(--brand-red)" d="M6.6 10.8a15.1 15.1 0 0 0 6.6 6.6l2.2-2.2a1 1 0 0 1 1-.25 11.4 11.4 0 0 0 3.6.57 1 1 0 0 1 1 1V20a1 1 0 0 1-1 1A17 17 0 0 1 3 4a1 1 0 0 1 1-1h3.5a1 1 0 0 1 1 1c0 1.25.2 2.45.57 3.6a1 1 0 0 1-.25 1z"/>
          </svg>
          0418563207
        </span>
      </address>
    </section>

    <section class="card card-back" aria-label="Card back">
      <div class="back-brand">
        <span class="back-dot"></span>
        <span class="back-name">PANHEARTH</span>
      </div>
      <p class="website">www.panhearth.com.au</p>
    </section>
  </main>
</body>
</html>
```